Website Design Required For Education Video Portfolio Site

I am looking for a designer to create a skin for a relaunch of my website - www.brackenlearningfilms.co.uk. We want a clean and stylish new design.

The website showcases prospectus/promotional videos that are made for schools and colleges. Videos will be hosted on YouTube and embedded.

I want it to be stylish and clean.

I require 7 pages designed and this must be agreed in order to do the project.

1. Homepage
2. About
3. Prices
4. Testimonials
5. Contact Page with form
6. Promotional Videos
7. Subject Videos

The website will be then be built on the Wordpress system.

Target Market(s)

Education, Schools, Colleges, Universities

Industry/Entity Type

Education

Font styles to use
Serif

Colors

Designer to choose colors to be used in the design.

Requirements
Must have
• Video content, be clean, show our portfolio, descriptions about videos. I like the idea of having video headers.
Nice to have
• Images

```html
<!DOCTYPE html>
<html lang="en">
<head>
<meta charset="utf-8">
<title>Bracken Learning Films</title>
<link href="https://fonts.googleapis.com/css2?family=Roboto:wght@400;500;700;900&display=swap" rel="stylesheet">
<style>
:root{
  --blue:#1aa9e1;
  --ink:#1b1b1b;
  --grey:#555;
  --pale:#eef7fb;
  --black:#0b0b0b;
  --white:#fff;
}
*{box-sizing:border-box;margin:0;padding:0}
html,body{width:1200px;height:4717px;overflow:hidden}
body{position:relative;background:var(--white);font-family:'Roboto',Arial,sans-serif;color:var(--ink)}
.abs{position:absolute}
.btn{position:absolute;background:var(--blue);color:var(--white);font-size:15px;letter-spacing:2px;display:flex;align-items:center;justify-content:center;border-radius:4px}
.h2{position:absolute;left:0;width:1200px;text-align:center;color:var(--blue);font-weight:700;font-size:42px;letter-spacing:5px}
.lead{position:absolute;text-align:center;color:var(--grey);font-size:15px;line-height:26px;letter-spacing:1px}

/* header */
.header{left:0;top:0;width:1200px;height:100px;background:var(--white);z-index:3}
.brand{left:112px;top:24px;display:flex;align-items:center;gap:10px}
.brand-mark{width:44px;height:44px;border-radius:50%;background:var(--blue)}
.brand-name{font-size:30px;font-weight:700;color:var(--blue);letter-spacing:.5px}
.nav{left:423px;top:38px;display:flex;gap:36px;font-size:16px;letter-spacing:2.5px;color:#333}
.search{left:1060px;top:37px}

/* hero */
.hero{left:0;top:95px;width:1200px;height:712px}
.hero-photo{left:0;top:0;width:1200px;height:712px;background:linear-gradient(90deg,#3d5d80 0%,#8a98a8 30%,#d8d3cc 55%,#f3efe9 70%,#f6f3ee 100%)}
.hero-mark{left:810px;top:110px;width:50px;height:50px;border-radius:50%;background:#111}
.welcome{left:560px;width:550px;top:190px;text-align:center;font-size:40px;font-weight:700;letter-spacing:5px}
.hero-title{left:560px;width:550px;top:240px;text-align:center;font-size:102px;font-weight:900;color:var(--blue);letter-spacing:4px;line-height:120px}
.hero-sub{left:560px;width:550px;top:380px;text-align:center;font-size:44px;letter-spacing:10px}

/* prices */
.card{position:absolute;top:1053px;width:310px;height:440px;background:var(--white);box-shadow:0 2px 8px rgba(0,0,0,.25);border-radius:4px;overflow:hidden}
.card-img{position:absolute;left:4px;top:4px;width:302px;height:207px}
.card-title{position:absolute;left:0;top:232px;width:310px;text-align:center;font-size:21px;font-weight:700;letter-spacing:2px;line-height:26px}
.card-text{position:absolute;left:0;top:300px;width:310px;text-align:center;font-size:15px;letter-spacing:1.5px;line-height:26px;color:#333}
.card .btn{left:86px;top:367px;width:138px;height:42px}

/* about */
.about-photo{left:0;top:1669px;width:587px;height:645px;background:linear-gradient(135deg,#6f6f6f,#3a3a3a 45%,#c9a52e 70%,#8a6a4c)}
.about-panel{left:587px;top:1669px;width:613px;height:645px;background:var(--pale)}
.about-title{left:682px;top:1725px;font-size:42px;font-weight:700;color:var(--blue);letter-spacing:5px}
.about-intro{left:680px;top:1805px;width:420px;font-size:21px;line-height:30px;letter-spacing:2px}
.about-body{left:682px;top:1955px;width:412px;font-size:15px;line-height:26px;letter-spacing:1.5px;color:#555}

/* promo */
.promo{position:absolute;top:2580px;width:291px;height:224px}
.promo-img{position:absolute;left:0;top:0;width:291px;height:196px}
.promo-label{position:absolute;left:13px;top:168px;width:265px;height:56px;background:var(--white);box-shadow:0 2px 6px rgba(0,0,0,.2);color:var(--blue);font-size:14px;font-weight:500;display:flex;align-items:center;justify-content:center}
.arrow{position:absolute;width:34px;height:34px;border-radius:50%;background:#111;display:flex;align-items:center;justify-content:center}

/* subject */
.subject-title{left:110px;top:2885px;font-size:42px;font-weight:700;color:var(--blue)}
.subject{position:absolute;width:225px;border-radius:6px}

/* testimonials */
.t-title{left:0;width:1200px;top:3372px;text-align:center;font-size:42px;font-weight:700;color:var(--blue)}
.t-card{left:403px;top:3469px;width:381px;height:200px;background:var(--blue);color:var(--white)}
.t-quote{position:absolute;font-size:15px;line-height:26px;text-align:center;color:#333}
.avatar{position:absolute;width:86px;height:86px;border-radius:50%;background:#b9c4cc;border:3px solid var(--white);box-shadow:0 1px 4px rgba(0,0,0,.2)}
.t-name{position:absolute;width:340px;text-align:center;font-size:15px;line-height:24px;color:#333}
.t-name b{display:block;color:var(--blue);font-weight:500}

/* contact */
.dark-band{left:0;top:4105px;width:1200px;height:612px;background:var(--black)}
.contact-left{left:112px;top:3914px;width:388px;height:334px;background:linear-gradient(180deg,#3a3a3a,#1d1d1d)}
.contact-right{left:500px;top:3914px;width:588px;height:334px;background:var(--blue)}
.field{position:absolute;color:var(--white);font-size:15px;border-bottom:1px solid rgba(255,255,255,.8);padding-bottom:18px}

/* footer */
.f-head{position:absolute;color:var(--white);font-weight:700}
.f-text{position:absolute;color:var(--white);font-size:20px;line-height:36px;letter-spacing:1px}
.social{position:absolute;width:34px;height:34px;border-radius:50%;background:var(--white)}
.legal{position:absolute;top:4685px;color:var(--white);font-size:13px}
</style>
</head>
<body>

<!-- hero -->
<section class="abs hero">
  <div class="abs hero-photo" role="img" aria-label="Smiling man with glasses writing in a notebook at a desk"></div>
  <div class="abs hero-mark"></div>
  <div class="abs welcome">Welcome to</div>
  <div class="abs hero-title">Bracken</div>
  <div class="abs hero-sub">Learning Films</div>
  <div class="btn" style="left:732px;top:568px;width:206px;height:42px">Watch Our Videos</div>
  <svg class="abs" style="left:0;top:692px" width="1200" height="30" viewBox="0 0 1200 30" aria-hidden="true">
    <polygon fill="#fff" points="0,10 60,16 120,8 200,18 280,9 360,15 440,7 520,17 600,10 680,16 760,8 840,18 920,9 1000,15 1080,7 1150,14 1200,9 1200,30 0,30"/>
  </svg>
</section>

<header class="abs header">
  <div class="abs brand"><span class="brand-mark"></span><span class="brand-name">Bracken</span></div>
  <nav class="abs nav"><span>Home</span><span>About</span><span>Prices</span><span>Testimonials</span><span>Contact</span><span>More ⌄</span></nav>
  <svg class="abs search" width="24" height="24" viewBox="0 0 24 24"><circle cx="10" cy="10" r="7" fill="none" stroke="#1aa9e1" stroke-width="3"/><line x1="15" y1="15" x2="22" y2="22" stroke="#1aa9e1" stroke-width="3"/></svg>
  <svg class="abs" style="left:0;top:90px" width="1200" height="20" viewBox="0 0 1200 20" aria-hidden="true">
    <polygon fill="#fff" points="0,0 1200,0 1200,8 1120,14 1040,6 960,13 880,5 800,12 720,6 640,14 560,7 480,13 400,5 320,12 240,6 160,14 80,7 0,12"/>
  </svg>
</header>

<!-- price guide -->
<h2 class="h2" style="top:880px">Price Guide</h2>
<p class="lead" style="left:300px;width:600px;top:942px">Offering affordable video content to schools, colleges and training providers in the North of England.</p>

<div class="card" style="left:110px">
  <div class="card-img" role="img" aria-label="Pupil playing a trumpet in a school band" style="background:linear-gradient(135deg,#1d3fa8,#3b5ed0 50%,#c99a3c)"></div>
  <div class="card-title">Subject Videos –<br>prices start at £1,200</div>
  <div class="card-text">15 videos – £1,200<br>20 videos – £1,400</div>
  <div class="btn">Buy Now</div>
</div>
<div class="card" style="left:443px">
  <div class="card-img" role="img" aria-label="Aerial view of a group walking across green fields" style="background:linear-gradient(180deg,#8eb49a,#5f8f3e 40%,#4a7a2c)"></div>
  <div class="card-title">Residential Videos –<br>prices start at £500</div>
  <div class="card-text">1/2 Day Filming – from £500<br>1 Days Filming – from £800</div>
  <div class="btn">Buy Now</div>
</div>
<div class="card" style="left:777px">
  <div class="card-img" role="img" aria-label="Stage microphone under blue spotlights" style="background:radial-gradient(circle at 55% 35%,#cfe6ff,#2c67b8 40%,#071a3a)"></div>
  <div class="card-title">Live Performance Filming<br>– prices start at £450</div>
  <div class="card-text">60-minute performance –<br>prices start at £450</div>
  <div class="btn">Buy Now</div>
</div>
<div class="btn" style="left:531px;top:1540px;width:138px;height:42px">View All</div>

<!-- about -->
<div class="abs about-photo" role="img" aria-label="Student in a yellow top working on a laptop surrounded by books"></div>
<div class="abs about-panel"></div>
<h2 class="abs about-title">About Us</h2>
<p class="abs about-intro">Hi, I’m Owen Rathley, Videographer, Content Creator, Filmmaker. Founder of Bracken Learning Films and dad of two. Thanks for stopping by.</p>
<p class="abs about-body">I’ve been producing all kinds of videos for over 25 years (from weddings and other live events to corporate and educational promotions – it’s truly the best job in the world). At the age of eight, I was bitten by the videomaking bug and went on to study it at college and, later, degree level. And it’s clearly still a big part of my life today.</p>
<div class="btn" style="left:682px;top:2202px;width:138px;height:42px">Read More</div>

<!-- promotional videos -->
<h2 class="h2" style="top:2394px">Promotional Videos</h2>
<p class="lead" style="left:280px;width:640px;top:2464px;font-size:14px;letter-spacing:0">Duis aute irure dolor in reprehenderit in voluptate velit esse cillum dolore eu fugiat nulla pariatur. Excepteur sint occaecat cupidatat non proident, sunt in culpa qui officia deserunt mollit anim id est laborum.</p>
<div class="arrow" style="left:57px;top:2664px"><svg width="14" height="14" viewBox="0 0 14 14"><path d="M9 2 4 7l5 5" stroke="#fff" stroke-width="2.5" fill="none"/></svg></div>
<div class="arrow" style="left:1106px;top:2664px"><svg width="14" height="14" viewBox="0 0 14 14"><path d="M5 2l5 5-5 5" stroke="#fff" stroke-width="2.5" fill="none"/></svg></div>
<div class="promo" style="left:110px"><div class="promo-img" role="img" aria-label="Pupils and teacher in a classroom" style="background:linear-gradient(135deg,#a8b3b8,#6b7c6a 50%,#d9d2c4)"></div><div class="promo-label">Birchwood Primary School</div></div>
<div class="promo" style="left:453px"><div class="promo-img" role="img" aria-label="Aerial view of a school campus among fields" style="background:linear-gradient(180deg,#7f9a6f,#b5aa94 50%,#6f8a5a)"></div><div class="promo-label">The Meadowbank Academy</div></div>
<div class="promo" style="left:795px"><div class="promo-img" role="img" aria-label="Children working together at a classroom table" style="background:linear-gradient(135deg,#6a5a4c,#a98d74 50%,#d9cbb8)"></div><div class="promo-label">Harbourside Primary School</div></div>

<!-- subject videos -->
<h2 class="abs subject-title">Subject Videos</h2>
<div class="arrow" style="left:1010px;top:2891px"><svg width="14" height="14" viewBox="0 0 14 14"><path d="M9 2 4 7l5 5" stroke="#fff" stroke-width="2.5" fill="none"/></svg></div>
<div class="arrow" style="left:1054px;top:2891px"><svg width="14" height="14" viewBox="0 0 14 14"><path d="M5 2l5 5-5 5" stroke="#fff" stroke-width="2.5" fill="none"/></svg></div>
<div class="subject" role="img" aria-label="Pupils in a classroom" style="left:-140px;top:2977px;height:283px;background:linear-gradient(160deg,#8c7a68,#c7b39a)"></div>
<div class="subject" role="img" aria-label="Girls writing at a school desk" style="left:112px;top:3010px;height:283px;background:linear-gradient(160deg,#a6937e,#d8c8b2)"></div>
<div class="subject" role="img" aria-label="Teacher helping students in class" style="left:363px;top:2977px;height:283px;background:linear-gradient(160deg,#6b6150,#b9a886)"></div>
<div class="subject" role="img" aria-label="Teacher standing in front of a class" style="left:614px;top:3010px;height:283px;background:linear-gradient(160deg,#4a4f55,#9a9790)"></div>
<div class="subject" role="img" aria-label="Smiling pupil at her desk" style="left:864px;top:2977px;height:283px;background:linear-gradient(160deg,#9fb0b8,#d8d0c4)"></div>
<div class="subject" role="img" aria-label="Student reading in class" style="left:1116px;top:3010px;height:283px;background:linear-gradient(160deg,#8a7262,#cbb59e)"></div>

<!-- testimonials -->
<h2 class="abs t-title">Our Testimonials</h2>
<svg class="abs" style="left:217px;top:3538px" width="56" height="34" viewBox="0 0 56 34"><circle cx="12" cy="20" r="12" fill="#111"/><circle cx="40" cy="20" r="12" fill="#111"/><path d="M2 18 12 0h6L10 18zM30 18 40 0h6l-8 18z" fill="#111"/></svg>
<p class="t-quote" style="left:104px;width:280px;top:3598px">A huge thanks to Owen for producing a fabulous promotional video for our school website.</p>
<div class="avatar" role="img" aria-label="Portrait of the head teacher" style="left:201px;top:3682px"></div>
<p class="t-name" style="left:74px;top:3783px">Carol Hensby, Head Teacher<b>Fellside Primary School</b></p>

<div class="abs t-card">
  <svg class="abs" style="left:164px;top:22px" width="56" height="34" viewBox="0 0 56 34"><circle cx="12" cy="20" r="12" fill="#fff"/><circle cx="40" cy="20" r="12" fill="#fff"/><path d="M2 18 12 0h6L10 18zM30 18 40 0h6l-8 18z" fill="#fff"/></svg>
  <p class="abs" style="left:50px;top:72px;width:281px;text-align:center;font-size:15px;line-height:26px">“We have found working with Bracken Learning Films a very easy and supportive process.</p>
</div>
<div class="avatar" role="img" aria-label="Portrait of the head teacher" style="left:550px;top:3630px"></div>
<p class="t-name" style="left:423px;top:3736px">Daniel Forsyth, Head Teacher<b>Larchfield Primary School, Redburn</b></p>

<svg class="abs" style="left:921px;top:3538px" width="56" height="34" viewBox="0 0 56 34"><circle cx="12" cy="20" r="12" fill="#111"/><circle cx="40" cy="20" r="12" fill="#111"/><path d="M2 18 12 0h6L10 18zM30 18 40 0h6l-8 18z" fill="#111"/></svg>
<p class="t-quote" style="left:804px;width:290px;top:3598px">The recording process ran very smoothly in school and I was very impressed with how much we managed to fit into a day!</p>
<div class="avatar" role="img" aria-label="Portrait of the head teacher" style="left:906px;top:3682px"></div>
<p class="t-name" style="left:779px;top:3783px">Helen Marsden, Head Teacher<b>Oakhurst Primary School</b></p>

<!-- contact -->
<div class="abs dark-band"></div>
<svg class="abs" style="left:0;top:4090px" width="1200" height="24" viewBox="0 0 1200 24" aria-hidden="true"><polygon fill="#0b0b0b" points="0,12 70,6 150,14 230,5 310,13 390,7 470,15 550,6 630,13 710,5 790,14 870,7 950,13 1030,5 1110,12 1200,6 1200,24 0,24"/></svg>
<div class="abs contact-left" role="img" aria-label="Teacher with pupils in a dim classroom"></div>
<h2 class="abs" style="left:112px;width:388px;top:3985px;text-align:center;color:#fff;font-size:40px;font-weight:700">Contact Us</h2>
<p class="abs" style="left:170px;width:272px;top:4045px;text-align:center;color:#fff;font-size:15px;line-height:26px">We love to listen and hear about your school or college. Please get in touch with us if you have any queries and we will get back to you as soon as possible.</p>
<div class="abs contact-right"></div>
<div class="field" style="left:542px;top:3960px;width:220px">First Name</div>
<div class="field" style="left:838px;top:3960px;width:220px">Last Name</div>
<div class="field" style="left:542px;top:4030px;width:220px">E-Mail</div>
<div class="field" style="left:838px;top:4030px;width:220px">Phone</div>
<div class="field" style="left:542px;top:4098px;width:516px">Message</div>
<div class="abs" style="left:544px;top:4162px;width:138px;height:42px;border:2px solid #fff;border-radius:4px;background:#fff;color:var(--blue);font-size:15px;letter-spacing:2px;display:flex;align-items:center;justify-content:center">Submit</div>

<!-- footer -->
<footer>
  <h3 class="f-head" style="left:110px;top:4313px;font-size:19px">Our Mission</h3>
  <p class="f-text" style="left:110px;top:4358px;width:260px;font-size:19px;line-height:24px;letter-spacing:0">Striving to deliver quality video content for schools and colleges in the North of England.</p>
  <div class="social" style="left:112px;top:4488px"></div>
  <div class="social" style="left:158px;top:4488px"></div>
  <div class="social" style="left:204px;top:4488px"></div>

  <h3 class="f-head" style="left:487px;top:4306px;font-size:27px">About Us</h3>
  <p class="f-text" style="left:487px;top:4354px">Home<br>About<br>Prices<br>Testimonials<br>Contact<br>Promotional Videos<br>Subject Videos</p>

  <h3 class="f-head" style="left:788px;top:4306px;font-size:27px">Contact Us</h3>
  <svg class="abs" style="left:757px;top:4365px" width="16" height="16" viewBox="0 0 16 16"><path d="M3 1h3l1.5 4-2 1.2a9 9 0 0 0 4.3 4.3L11 8.5l4 1.5v3a2 2 0 0 1-2 2A13 13 0 0 1 1 3a2 2 0 0 1 2-2z" fill="#fff"/></svg>
  <svg class="abs" style="left:757px;top:4402px" width="16" height="12" viewBox="0 0 16 12"><rect width="16" height="12" fill="#fff"/><path d="M0 0l8 6 8-6" stroke="#0b0b0b" stroke-width="1.5" fill="none"/></svg>
  <svg class="abs" style="left:758px;top:4436px" width="14" height="18" viewBox="0 0 14 18"><path d="M7 0a7 7 0 0 1 7 7c0 5-7 11-7 11S0 12 0 7a7 7 0 0 1 7-7z" fill="#fff"/><circle cx="7" cy="7" r="2.5" fill="#0b0b0b"/></svg>
  <p class="f-text" style="left:788px;top:4354px;width:320px">07000 123 456<br>info@brackenlearningfilms.co.uk<br>Studio 4, Kestrel Business Park, Ashby Vale. AV1 2XY.</p>

  <div class="abs" style="left:0;top:4665px;width:1200px;border-top:1px solid #333"></div>
  <p class="legal" style="left:110px">Company Registration Number: 00000000.</p>
  <p class="legal" style="left:700px">© Bracken Learning Films Limited 2023. All Rights Reserved.</p>
</footer>

</body>
</html>
```